Business card design needed

I would like a one sided black business card with the information provided above. Refer to my website www.brightvolleyracquets.com.au for an example of colors I have used for my site, would like to keep this consistent for my business cards also, I will upload my logo below.

I am a new small business that provides tennis customers with racquet re stringing, tennis strings and accessories.

Industry/Entity Type

Small Business

Contact Information for Business Card

Bright Volley Tennis

Owen Whitby
Managing Director

brightvolleyracquets@mailbox.example
www.brightvolleyracquets.com.au
0491 726 305

Racquet Restringing/Tennis Strings/Accessories

Requirements
Must have
• Must have my logo and card must be black

```html
<!DOCTYPE html>
<html lang="en">
<head>
<meta charset="utf-8">
<title>Bright Volley Tennis – Business Card</title>
<link rel="stylesheet" href="https://fonts.googleapis.com/css2?family=Montserrat:wght@400;600&display=swap">
<style>
  :root {
    --stage: #ece7e1;
    --card-black: #000000;
    --lime: #c5dc3a;
    --lime-soft: #b9d45a;
    --court-blue: #2d4f86;
    --white: #ffffff;
  }
  * { box-sizing: border-box; margin: 0; padding: 0; }
  html, body {
    width: 1200px; height: 475px; overflow: hidden;
    background: var(--stage);
    font-family: "Montserrat", Arial, sans-serif;
  }
  .sheet { position: relative; width: 1200px; height: 475px; }
  .card {
    position: absolute; top: 82px;
    width: 545px; height: 312px;
    background: var(--card-black);
    border-radius: 16px; overflow: hidden;
  }
  .card--front { left: 36px; }
  .card--back { left: 607px; }

  .brand {
    position: absolute; display: flex; align-items: center; gap: 12px;
    color: var(--lime); font-weight: 600; text-transform: uppercase;
    letter-spacing: 1px; white-space: nowrap;
  }
  .brand__dot { width: 30px; height: 30px; border-radius: 50%; background: var(--lime); flex: none; }
  .card--front .brand { left: 46px; top: 62px; font-size: 25px; }
  .card--back .brand { left: 0; right: 0; top: 122px; justify-content: center; font-size: 28px; }

  .contact { position: absolute; left: 44px; top: 164px; list-style: none; }
  .contact__item {
    display: flex; align-items: center; gap: 12px;
    color: var(--white); font-size: 14.5px; font-weight: 400;
    height: 19px; margin-bottom: 2px; letter-spacing: .2px;
  }
  .contact__icon { width: 12px; height: 12px; flex: none; }

  .swoosh { position: absolute; left: 0; top: 0; width: 545px; height: 312px; }

  .person { position: absolute; right: 30px; top: 250px; text-align: right; }
  .person__name { color: var(--lime-soft); font-size: 18px; font-weight: 400; letter-spacing: .3px; }
  .person__role { color: var(--lime); font-size: 13.5px; font-weight: 400; margin-top: 2px; }

  .web {
    position: absolute; left: 0; right: 0; top: 242px; text-align: center;
    color: var(--white); font-size: 14px; letter-spacing: 2px;
  }
</style>
</head>
<body>
<main class="sheet">
  <section class="card card--front">
    <svg class="swoosh" viewBox="0 0 545 312" aria-hidden="true">
      <path d="M0,228 Q290,296 545,150 L545,312 L0,312 Z" fill="var(--lime)"/>
      <path d="M0,239 Q300,300 545,163 L545,312 L0,312 Z" fill="var(--card-black)"/>
      <path d="M0,244 Q300,304 545,170 L545,312 L0,312 Z" fill="var(--court-blue)"/>
    </svg>

    <div class="brand"><span class="brand__dot"></span>Bright Volley Tennis</div>

    <ul class="contact">
      <li class="contact__item">
        <svg class="contact__icon" viewBox="0 0 12 12" aria-hidden="true">
          <circle cx="6" cy="6" r="6" fill="var(--lime)"/>
          <path d="M3.6,3 L5,3 L5.4,4.6 L4.6,5.2 Q5.3,6.7 6.8,7.4 L7.4,6.6 L9,7 L9,8.4 Q5,8.8 3.6,3 Z" fill="var(--card-black)"/>
        </svg>
        0491 726 305
      </li>
      <li class="contact__item">
        <svg class="contact__icon" viewBox="0 0 12 12" aria-hidden="true">
          <rect x="0.5" y="2.5" width="11" height="7.5" rx="1" fill="var(--lime)"/>
          <path d="M1,3 L6,7 L11,3" fill="none" stroke="var(--card-black)" stroke-width="1"/>
        </svg>
        brightvolleyracquets@mailbox.example
      </li>
      <li class="contact__item">
        <svg class="contact__icon" viewBox="0 0 12 12" aria-hidden="true">
          <circle cx="6" cy="6" r="5.5" fill="var(--lime)"/>
          <g fill="none" stroke="var(--card-black)" stroke-width=".8">
            <ellipse cx="6" cy="6" rx="2.4" ry="5.5"/>
            <line x1="0.5" y1="6" x2="11.5" y2="6"/>
            <line x1="1.5" y1="3.5" x2="10.5" y2="3.5"/>
            <line x1="1.5" y1="8.5" x2="10.5" y2="8.5"/>
          </g>
        </svg>
        www.brightvolleyracquets.com.au
      </li>
    </ul>

    <div class="person">
      <p class="person__name">OWEN WHITBY</p>
      <p class="person__role">Managing Director</p>
    </div>
  </section>

  <section class="card card--back">
    <div class="brand"><span class="brand__dot"></span>Bright Volley Tennis</div>
    <p class="web">www.brightvolleyracquets.com.au</p>
  </section>
</main>
</body>
</html>
```